Elegant, Playful ReDesign of Paperlynx Website in wordpress - Budget has been raised

Project Brief: Paperlynx Website Redesign in WordPress

Introduction: Paperlynx, a cutting-edge document creation solution, aims to revolutionize the tedious process of crafting contracts, offers, forms, and other documents. By saving customers valuable time, streamlining workflows, and minimizing human error, Paperlynx has become an essential tool. As a technology company with a diverse clientele, we're set to boost our online presence through a refreshed WordPress website. Beyond a modernized website, we aspire to establish a stronger brand identity, incorporating graphic elements seamlessly into our online presence.

Current Status: Currently hosted on WordPress, Paperlynx's existing website serves its purpose but is ready for a visual transformation. Our goal is to maintain a modern and attractive appearance while upholding our commitment to simplicity and efficiency. Notably, the website is currently only in Danish. The redesigned structure should include a language switch function to cater to future international customers.

Objectives:
• Modern Aesthetic: Redesign the website with a fresh and modern vibe, reflecting innovation in the document creation sphere.
• User-Friendly: Prioritize an intuitive design for seamless navigation, ensuring visitors easily understand our offerings and benefits.
• Informative Content: Strike a balance between attractiveness and informativeness, clearly communicating Paperlynx's value proposition and simplifying business processes.
• Graphic Elements: Integrate visually appealing graphics that enhance the site's aesthetics and contribute to our overall visual identity. These elements should be versatile for future use in social media, advertisements, and other branding materials.
• Brand Recognition: Maintain our current logo and color scheme while exploring creative ways to establish a distinctive brand identity. The website should be a cornerstone for a cohesive branding strategy.
• Media Integration: Include images or videos on the website to enhance engagement. Find suitable, free-to-use visuals.
• Responsiveness: Ensure the design is responsive and works seamlessly on all devices.
• Demo Booking Form: Improve the design of the form to book a demo.
• Multilingual Support: Enable language transformation; the website is currently in Danish but should cater to other countries.

Guidelines:
• Typography: Up to the designer's discretion.
• Images/Videos: Must be free to use without additional charges.
• WordPress Theme: Use any WordPress theme below $100.
• Logo Redesign: Not needed; stick to the referenced color palette, as our new logo uses these colors.
• Color Palette: Stick to the existing company colors for consistency:
RGB
• #000b3c
• #004c6c
• #319ac3
• Greytones and white are also allowed
• Creativity Encouraged: Embrace creativity within the color palette for the layout, visuals, and overall user experience.

Conclusion: The Paperlynx website redesign marks an exciting opportunity to enhance our online presence. Our goal is to achieve a balance between a modern, attractive design and a clear, informative representation of our innovative solutions. We envision the revamped website as the foundation for a compelling online brand presence, with versatile graphic elements resonating across various digital platforms.

Sections that the website must include: Space for customer logos, space for testimonials, Space and redesign for display of price structure and price comparison, sections for company details and other information.

Design should also include a redesign of the customer cases section.
Generally there should just be a redesign of all things that are on the website.

Link to current website: https://paperlynx.example/

Target Market(s)

+50 employees.

Industry/Entity Type

Document automation

Coding

Coded - Design and coding required

Number of Pages Required

5+ page

Colors
0054AA
0677BA
7BADD7
CADEEF
E8F1F8

Requirements
Must have
• The new webpage must have the same pages as the current one. Frontpage, Book demo, About us, Case stories and Pricing

```html
<!DOCTYPE html>
<html lang="en">
<head>
<meta charset="utf-8">
<title>Paperlynx — Create Error-free Contracts and Quotes Quickly</title>
<link rel="stylesheet" href="https://fonts.googleapis.com/css2?family=Roboto:wght@400;500;700;900&family=Roboto+Condensed:wght@400;500;700&display=swap">
<style>
  :root {
    --navy: #000b3c;
    --deep: #004c6c;
    --sky: #319ac3;
    --login: #1a9fe0;
    --ink: #111418;
    --white: #ffffff;
    --muted: #e9eef2;
  }
  * { box-sizing: border-box; margin: 0; padding: 0; }
  html, body { width: 1200px; height: 717px; overflow: hidden; background: var(--white); }
  body { font-family: "Roboto", Arial, sans-serif; color: var(--ink); position: relative; }

  .hero-backdrop { position: absolute; left: 0; top: 0; width: 1200px; height: 590px; }

  .site-header { position: absolute; left: 0; top: 0; width: 1200px; height: 90px; }
  .brand { position: absolute; left: 86px; top: 30px; display: flex; align-items: center; gap: 10px; }
  .brand-mark { width: 34px; height: 34px; background: var(--sky); }
  .brand-name { font-family: "Roboto", Arial, sans-serif; font-weight: 700; font-size: 28px; color: var(--deep); letter-spacing: 0.2px; }

  .main-nav { position: absolute; right: 62px; top: 50px; display: flex; align-items: center; gap: 10px; }
  .main-nav a { color: var(--white); text-decoration: none; font-size: 12.5px; font-weight: 500; padding: 4px 6px; line-height: 14px; }
  .main-nav .is-current { border: 1px solid var(--white); padding: 4px 12px; }
  .main-nav .login { background: var(--login); padding: 5px 12px; }
  .main-nav .lang { display: flex; align-items: center; gap: 5px; }

  .hero-visual { position: absolute; left: 86px; top: 207px; width: 580px; height: 383px;
    background: linear-gradient(160deg, #eef1f4 0%, #d7dde3 55%, #9fb3c2 100%); border-radius: 4px; }

  .hero-copy { position: absolute; left: 740px; top: 168px; color: var(--white); }
  .hero-title { font-weight: 900; font-size: 41px; line-height: 46px; letter-spacing: 0.2px; }
  .hero-points { list-style: none; margin-top: 38px; }
  .hero-points li { font-family: "Roboto Condensed", Arial, sans-serif; font-size: 20px; font-weight: 500; line-height: 34.5px; }
  .hero-points li::before { content: "•"; font-size: 12px; margin-right: 6px; vertical-align: 3px; }

  .features { position: absolute; left: 0; top: 612px; width: 1200px; display: flex; justify-content: space-between; padding: 0 118px 0 100px; }
  .feature { width: 300px; text-align: center; }
  .feature svg { display: block; margin: 0 auto 6px; }
  .feature h3 { font-family: "Roboto Condensed", Arial, sans-serif; font-weight: 700; font-size: 18px; color: var(--ink); letter-spacing: 0.3px; }
  .feature p { font-family: "Roboto Condensed", Arial, sans-serif; font-size: 12.5px; line-height: 14px; color: var(--ink); margin-top: 2px; }
</style>
</head>
<body>

<svg class="hero-backdrop" viewBox="0 0 1200 590" role="img" aria-label="Background photo of a business person working with documents, tinted in deep blue">
  <defs>
    <linearGradient id="heroTint" x1="0" y1="0" x2="1" y2="1">
      <stop offset="0" stop-color="#2d5a78"/>
      <stop offset="0.45" stop-color="#0f4466"/>
      <stop offset="1" stop-color="#0a3454"/>
    </linearGradient>
  </defs>
  <path d="M430 0 H1200 V590 H360 C 360 470, 370 330, 400 200 C 410 120, 420 50, 430 0 Z" fill="url(#heroTint)"/>
</svg>

<header class="site-header">
  <div class="brand">
    <span class="brand-mark"></span>
    <span class="brand-name">Paperlynx</span>
  </div>
  <nav class="main-nav">
    <a class="is-current" href="#">Home</a>
    <a href="#">Customer Cases</a>
    <a href="#">Video</a>
    <a href="#">Live Demo</a>
    <a href="#">Prices</a>
    <a href="#">About Us</a>
    <a class="login" href="#">Login</a>
    <a class="lang" href="#">English
      <svg width="10" height="6" viewBox="0 0 10 6"><path d="M0 0 H10 L5 6 Z" fill="#ffffff"/></svg>
    </a>
  </nav>
</header>

<div class="hero-visual" role="img" aria-label="Illustration of a desktop, tablet and phone showing file uploads, with a person working on a laptop"></div>

<section class="hero-copy">
  <h1 class="hero-title">Create Error-free<br>Contracts and<br>Quotes Quickly</h1>
  <ul class="hero-points">
    <li>Get Paragraphs Inserted Automatically</li>
    <li>Get Prices Calculated Automatically</li>
    <li>Eliminate Manual Work</li>
    <li>Sign Digitally</li>
  </ul>
</section>

<section class="features">
  <div class="feature">
    <svg width="50" height="50" viewBox="0 0 50 50" fill="none" stroke="#1a9fe0" stroke-width="2.5" stroke-linecap="round">
      <circle cx="25" cy="26" r="19"/>
      <circle cx="25" cy="26" r="14" stroke-width="1.5"/>
      <path d="M25 18 V26 L31 30"/>
      <path d="M38 8 L42 12"/>
    </svg>
    <h3>SAVE TIME</h3>
    <p>Reduce your time consumption by up to 90%<br>when creating customer contracts and offers.</p>
  </div>
  <div class="feature">
    <svg width="50" height="50" viewBox="0 0 50 50" fill="none" stroke="#1a9fe0" stroke-width="2.5" stroke-linejoin="round" stroke-linecap="round">
      <path d="M25 3 L31 8 L39 8 L41 16 L47 22 L43 29 L44 37 L36 40 L31 46 L25 43 L19 46 L14 40 L6 37 L7 29 L3 22 L9 16 L11 8 L19 8 Z"/>
      <circle cx="25" cy="25" r="11"/>
      <path d="M20 25 L24 29 L31 21"/>
    </svg>
    <h3>HIGH QUALITY</h3>
    <p>Automation gives you minimal work and<br>eliminates errors in your documents.</p>
  </div>
  <div class="feature">
    <svg width="60" height="50" viewBox="0 0 60 50" fill="none" stroke="#1a9fe0" stroke-width="2.2" stroke-linecap="round">
      <circle cx="14" cy="10" r="5"/>
      <rect x="24" y="5" width="22" height="10" rx="5"/>
      <rect x="10" y="20" width="26" height="10" rx="5"/>
      <rect x="14" y="35" width="22" height="10" rx="5"/>
      <path d="M46 10 H52 V25 H36"/>
      <path d="M10 25 H6 V40 H14"/>
      <circle cx="46" cy="40" r="6"/>
      <path d="M43 40 L45 42 L49 38"/>
    </svg>
    <h3>STREAMLINED FLOW</h3>
    <p>Be guided all the way through the document and<br>ask for review before signing.</p>
  </div>
</section>

</body>
</html>
```